Business cards for a fun web development agency

Hi,I am building a web development agency. You can read about it on the website http://kite-loft.examplehost.com. Basically, I want to focus on free and open source products and stay as far away from the corporate business feeling as possible. I want to build a community so I want the business card to feel fun and approachable (at the risk of professional if need be). I am uploading some of my image assets in various file formats. Feel free to use them or make your own if you want just keeping in theme with the website.
Industry/Entity Type
Building
Contact Information for Business Card
Company Name: Boat ShedWebsite: www.kiteloftdev.example (it's currently in alpha on http://kite-loft.examplehost.com if you want to see the them we are trying to capture)My name is: Banner B. SchaferMy email: banner@boatsheddev.comMy phone: 0431 587 904
Look and feel

```html
<!DOCTYPE html>
<html lang="en">
<head>
<meta charset="utf-8">
<title>Kite Loft – Business Card</title>
<link href="https://fonts.googleapis.com/css2?family=Arimo:wght@400&display=swap" rel="stylesheet">
<style>
  :root {
    --page: #e6e7e3;
    --card-top: #c8cac3;
    --card-bottom: #bfd39b;
    --brand-blue: #1282b4;
    --ink-blue: #1a80b6;
    --white: #ffffff;
  }
  html, body {
    margin: 0;
    padding: 0;
    width: 1200px;
    height: 902px;
    overflow: hidden;
    background: var(--page);
    font-family: "Arimo", Arial, sans-serif;
  }
  .business-card {
    position: absolute;
    left: 100px;
    top: 166px;
    width: 1000px;
    height: 570px;
    background: linear-gradient(180deg, var(--card-top) 0%, var(--card-top) 45%, var(--card-bottom) 100%);
    box-shadow: 0 6px 24px rgba(0,0,0,0.18);
    overflow: hidden;
  }
  .card-band {
    position: absolute;
    inset: 0;
    width: 1000px;
    height: 570px;
  }
  .card-band path { fill: var(--brand-blue); }
  .wordmark {
    position: absolute;
    top: 64px;
    left: 0;
    width: 100%;
    text-align: center;
    color: var(--brand-blue);
    font-size: 100px;
    line-height: 116px;
    letter-spacing: 2px;
    font-weight: 400;
    margin: 0;
  }
  .contact {
    position: absolute;
    top: 252px;
    left: 0;
    width: 100%;
    text-align: center;
    color: var(--white);
  }
  .contact-name {
    font-size: 43px;
    line-height: 56px;
    margin: 0 0 18px;
    font-weight: 400;
  }
  .contact-line {
    font-size: 28px;
    line-height: 36px;
    margin: 0;
  }
  .services {
    position: absolute;
    top: 504px;
    left: 0;
    width: 100%;
    display: flex;
    justify-content: center;
    align-items: center;
    margin: 0;
    padding: 0;
    list-style: none;
    color: var(--ink-blue);
    font-size: 22px;
    line-height: 32px;
  }
  .services li { padding: 0 9px; }
  .services li + li { border-left: 1.5px solid var(--ink-blue); }
</style>
</head>
<body>
  <main class="business-card">
    <svg class="card-band" viewBox="0 0 1000 570" aria-hidden="true">
      <path d="M0 186 Q500 300 1000 186 L1000 502 Q500 392 0 502 Z"/>
    </svg>

    <h1 class="wordmark">KITE LOFT</h1>

    <section class="contact">
      <p class="contact-name">Corwin T. Aldous</p>
      <p class="contact-line">0431 587 904</p>
      <p class="contact-line">www.kiteloftdev.example</p>
      <p class="contact-line">corwin@kiteloftdev.example</p>
    </section>

    <ul class="services">
      <li>Open Source Software</li>
      <li>Consulting For Developers</li>
      <li>Web Development For Muggles</li>
    </ul>
  </main>
</body>
</html>
```